Internal web page of multinational company - Portfolio of reports

We need to improve the look & feel of an existing internal HTML page.
We use it as a portfolios where users go and see a list of existing reports as "tiles". The HTML page is automatically generated by a javascript that reads the contents to display from an HTML file.
What is needs is a "face lift" in the design of the page.
Currently we use icons on the top right of each tile to denote the type of technology used on the report and also colons for the same purpose. The attached screenshots will be self explanatory.
Across the top we have "tabs" that, once selected change the tiles.
Need a proposal for new design that keeps is as clean as possible, specially the home page that should be very light (Plimbo like).
The idea for this page is to serve as a "one stop shop" and become a bookmark for everyone in the company.
Looking for a wow effect that make is visually

Target Market(s)

Internal employees

Industry/Entity Type

It Company

Coding

Coded - Design and coding required

Number of Pages Required

2 page

Requirements
Must have
• Should not change the logo or its position from the bottom left.
• Page must be as clean as possible and
Nice to have
• Welcome to change the logo on the top left. This page is from the CSU M&I (Mni) which stands for Central Support Unit - Metrics & Insight.
Should not have
• Do no use red, this is the color of our competitor. The blue on the bottom is standard for our logo

```html
<!DOCTYPE html>
<html lang="en">
<head>
<meta charset="utf-8">
<title>CSU M&amp;I – Report Portfolio</title>
<link href="https://fonts.googleapis.com/css2?family=Roboto+Condensed:wght@400;700&family=Open+Sans:wght@400;600&display=swap" rel="stylesheet">
<style>
:root{
  --page:#e9ecf0;
  --white:#ffffff;
  --brand:#3a73ab;
  --title:#2f6aa6;
  --orange:#ff7a00;
  --green:#2e9f6b;
  --muted:#6b7480;
  --line:#dde2e8;
  --btn:#f1f4f7;
  --marker:#7f97c6;
  --envelope:#c9cdd2;
}
*{box-sizing:border-box;margin:0;padding:0}
html,body{width:1200px;height:678px;overflow:hidden}
body{background:var(--page);font-family:"Open Sans",Arial,sans-serif;position:relative}

/* header */
.topbar{position:absolute;left:0;top:0;width:1200px;height:52px;background:var(--white);box-shadow:0 1px 2px rgba(0,0,0,.06)}
.brand{position:absolute;left:98px;top:13px;display:flex;align-items:center;gap:7px;font-family:"Roboto Condensed",sans-serif;font-size:22px;line-height:26px;color:var(--brand)}
.brand-dot{width:26px;height:26px;border-radius:50%;background:var(--brand)}
.nav-item{position:absolute;top:0;height:52px;display:flex;align-items:center;font-family:"Roboto Condensed",sans-serif;font-size:10.8px;color:var(--title);text-decoration:none;text-transform:uppercase;white-space:nowrap}
.nav-item svg{margin-left:4px}
.nav-item.active{left:235px;width:71px;justify-content:center;background:var(--brand);color:var(--white)}
.search{position:absolute;left:868px;top:12px;width:171px;height:29px;border:1px solid var(--line);border-radius:2px;padding:0 13px;font-size:11px;color:#8a9099;display:flex;align-items:center}
.icon-btn{position:absolute;top:12px;width:25px;height:29px;background:var(--btn);border:1px solid var(--line);border-radius:2px;display:flex;align-items:center;justify-content:center}

/* tiles */
.grid{position:absolute;left:98px;top:87px;display:grid;grid-template-columns:repeat(4,244px);grid-auto-rows:78px;column-gap:9px;row-gap:11px}
.tile{background:var(--white);border:1px solid var(--line);position:relative}
.tile-head{position:relative;z-index:1;display:flex;align-items:center;height:38px;padding:0 12px}
.marker{width:10px;height:10px;background:var(--marker);flex:none}
.tile.is-draft .marker{background:var(--orange)}
.tile.is-final .marker{background:#7fc6a8}
.envelope{width:13px;height:10px;background:var(--envelope);margin-left:3px;flex:none}
.tile-title{margin-left:6px;font-family:"Roboto Condensed",sans-serif;font-size:10.7px;color:var(--title);text-transform:uppercase;white-space:nowrap}
.tile.is-draft .tile-title{color:var(--orange)}
.tile.is-final .tile-title{color:var(--green)}
.tech{position:absolute;right:7px;top:5px;width:24px;height:24px;border-radius:2px}
.tech.viz{background:#eef0f3;border:1px solid #dfe3e8}
.tech.portal{background:#8fb7de}
.actions{position:absolute;right:6px;bottom:6px;display:flex;border:1px solid var(--line);border-radius:2px}
.actions span{width:31px;height:27px;background:var(--btn);display:flex;align-items:center;justify-content:center;border-left:1px solid var(--line)}
.actions span:first-child{border-left:0;width:34px}
.tile-band{position:absolute;left:0;right:0;top:38px;bottom:0;background:var(--orange)}

/* popover */
.popover{position:absolute;left:98px;top:443px;width:244px;height:83px;background:var(--white);border:1px solid var(--line);box-shadow:0 2px 4px rgba(0,0,0,.08);padding:15px 16px}
.popover::before{content:"";position:absolute;left:114px;top:-7px;width:12px;height:12px;background:var(--white);border-left:1px solid var(--line);border-top:1px solid var(--line);transform:rotate(45deg)}
.popover h3{font-family:"Roboto Condensed",sans-serif;font-weight:400;font-size:11px;color:var(--title);text-transform:uppercase}
.popover p{margin-top:3px;font-size:10px;line-height:20px;color:var(--muted)}

/* footer */
.footer{position:absolute;left:0;top:633px;width:1200px;height:45px;background:var(--brand)}
.help{position:absolute;left:98px;top:7px;width:140px;height:31px;border:1px solid var(--white);display:flex;align-items:center;justify-content:center;gap:9px;font-family:"Roboto Condensed",sans-serif;font-size:11.5px;color:var(--white)}
.copyright{position:absolute;left:255px;top:16px;font-size:8.5px;color:var(--white)}
.foot-brand{position:absolute;left:1013px;top:11px;display:flex;align-items:center;gap:6px;font-family:"Roboto Condensed",sans-serif;font-size:17px;color:var(--white)}
.foot-brand i{width:19px;height:19px;border-radius:50%;background:var(--white)}
.version{position:absolute;left:1166px;top:15px;font-size:11px;color:var(--white)}
</style>
</head>
<body>
<svg width="0" height="0" style="position:absolute">
  <symbol id="i-wrench" viewBox="0 0 12 12"><path d="M10.5 1.5a3 3 0 0 0-3.6 3.6L1.2 10.8l1 1L8 6.1a3 3 0 0 0 3.6-3.6L9.8 4.3 8.5 4 8.2 2.7z" fill="#2f6aa6"/></symbol>
  <symbol id="i-doc" viewBox="0 0 12 12"><path d="M2.5 .8h5l2.5 2.5v8H2.5z" fill="none" stroke="#2f6aa6" stroke-width="1"/><path d="M4 5h4.5M4 7h4.5M4 9h4.5" stroke="#2f6aa6" stroke-width=".9"/></symbol>
  <symbol id="i-chart" viewBox="0 0 12 12"><path d="M1 1v10h10.5" fill="none" stroke="#2f6aa6" stroke-width="1.1"/><path d="M3.5 5.5h1.4v4.5H3.5zM6 3h1.4v7H6zM8.5 4.5h1.4V10H8.5z" fill="#2f6aa6"/></symbol>
</svg>

<header class="topbar">
  <div class="brand"><span class="brand-dot"></span>CSUM&amp;I</div>
  <nav>
    <a class="nav-item active" href="#">Finance<svg width="8" height="5" viewBox="0 0 8 5"><path d="M1 1l3 3 3-3" fill="none" stroke="#fff" stroke-width="1.2"/></svg></a>
    <a class="nav-item" style="left:313px" href="#">GM View</a>
    <a class="nav-item" style="left:377px" href="#">Hub View</a>
    <a class="nav-item" style="left:447px" href="#">M1</a>
    <a class="nav-item" style="left:487px" href="#">General Accounting</a>
    <a class="nav-item" style="left:611px" href="#">Tax</a>
    <a class="nav-item" style="left:655px" href="#">Treasury</a>
    <a class="nav-item" style="left:727px" href="#">Knowledge</a>
    <a class="nav-item" style="left:816px" href="#">Filter<svg width="8" height="5" viewBox="0 0 8 5"><path d="M1 1l3 3 3-3" fill="none" stroke="#2f6aa6" stroke-width="1.2"/></svg></a>
  </nav>
  <div class="search">Search..</div>
  <div class="icon-btn" style="left:1043px"><svg width="12" height="12" viewBox="0 0 12 12"><circle cx="5" cy="5" r="3.7" fill="none" stroke="#2f6aa6" stroke-width="1.6"/><path d="M7.8 7.8l3 3" stroke="#2f6aa6" stroke-width="1.8"/></svg></div>
  <div class="icon-btn" style="left:1071px"><svg width="10" height="10" viewBox="0 0 10 10"><path d="M2 2l6 6M8 2l-6 6" stroke="#2f6aa6" stroke-width="2"/></svg></div>
</header>

<main class="grid">
  <article class="tile"><div class="tile-head"><span class="marker"></span><span class="envelope"></span><span class="tile-title">B&amp;AT Revenue &amp; Margin Analysis</span></div><span class="tech viz"></span><div class="actions"><span><svg width="12" height="12"><use href="#i-wrench"/></svg></span><span><svg width="12" height="12"><use href="#i-doc"/></svg></span><span><svg width="12" height="12"><use href="#i-chart"/></svg></span></div></article>
  <article class="tile is-draft"><div class="tile-head"><span class="marker"></span><span class="envelope"></span><span class="tile-title">Bolt</span></div><span class="tech portal"></span><div class="actions"><span><svg width="12" height="12"><use href="#i-wrench"/></svg></span><span><svg width="12" height="12"><use href="#i-doc"/></svg></span><span><svg width="12" height="12"><use href="#i-chart"/></svg></span></div></article>
  <article class="tile"><div class="tile-head"><span class="marker"></span><span class="envelope"></span><span class="tile-title">BSQ Dashboard</span></div><span class="tech viz"></span><div class="actions"><span><svg width="12" height="12"><use href="#i-wrench"/></svg></span><span><svg width="12" height="12"><use href="#i-doc"/></svg></span><span><svg width="12" height="12"><use href="#i-chart"/></svg></span></div></article>
  <article class="tile"><div class="tile-head"><span class="marker"></span><span class="envelope"></span><span class="tile-title">Globel JV Trends</span></div><span class="tech viz"></span><div class="actions"><span><svg width="12" height="12"><use href="#i-wrench"/></svg></span><span><svg width="12" height="12"><use href="#i-doc"/></svg></span><span><svg width="12" height="12"><use href="#i-chart"/></svg></span></div></article>

  <article class="tile"><div class="tile-head"><span class="marker"></span><span class="envelope"></span><span class="tile-title">Inventory Reconciliations</span></div><span class="tech portal"></span><div class="actions"><span><svg width="12" height="12"><use href="#i-wrench"/></svg></span><span><svg width="12" height="12"><use href="#i-doc"/></svg></span><span><svg width="12" height="12"><use href="#i-chart"/></svg></span></div></article>
  <article class="tile"><div class="tile-head"><span class="marker"></span><span class="envelope"></span><span class="tile-title">Norvik Inventory Indicators</span></div><span class="tech viz"></span><div class="actions"><span><svg width="12" height="12"><use href="#i-wrench"/></svg></span><span><svg width="12" height="12"><use href="#i-doc"/></svg></span><span><svg width="12" height="12"><use href="#i-chart"/></svg></span></div></article>
  <article class="tile"><div class="tile-head"><span class="marker"></span><span class="envelope"></span><span class="tile-title">MIBS Metrics</span></div><span class="tech portal"></span><div class="actions"><span><svg width="12" height="12"><use href="#i-wrench"/></svg></span><span><svg width="12" height="12"><use href="#i-doc"/></svg></span><span><svg width="12" height="12"><use href="#i-chart"/></svg></span></div></article>
  <article class="tile"><div class="tile-head"><span class="marker"></span><span class="envelope"></span><span class="tile-title">MI Negative Inventory</span></div><span class="tech viz"></span><div class="actions"><span><svg width="12" height="12"><use href="#i-wrench"/></svg></span><span><svg width="12" height="12"><use href="#i-doc"/></svg></span><span><svg width="12" height="12"><use href="#i-chart"/></svg></span></div></article>

  <article class="tile"><div class="tile-head"><span class="marker"></span><span class="envelope"></span><span class="tile-title">MI PCPR</span></div><span class="tech viz"></span><div class="actions"><span><svg width="12" height="12"><use href="#i-wrench"/></svg></span><span><svg width="12" height="12"><use href="#i-doc"/></svg></span><span><svg width="12" height="12"><use href="#i-chart"/></svg></span></div></article>
  <article class="tile"><div class="tile-head"><span class="marker"></span><span class="envelope"></span><span class="tile-title">MI PO Performance</span></div><span class="tech viz"></span><div class="actions"><span><svg width="12" height="12"><use href="#i-wrench"/></svg></span><span><svg width="12" height="12"><use href="#i-doc"/></svg></span><span><svg width="12" height="12"><use href="#i-chart"/></svg></span></div></article>
  <article class="tile is-draft"><div class="tile-head"><span class="marker"></span><span class="envelope"></span><span class="tile-title">NAM Balace Sheet Online Tool</span></div><span class="tech viz"></span><div class="actions"><span><svg width="12" height="12"><use href="#i-wrench"/></svg></span><span><svg width="12" height="12"><use href="#i-doc"/></svg></span><span><svg width="12" height="12"><use href="#i-chart"/></svg></span></div></article>
  <article class="tile is-final"><div class="tile-head"><span class="marker"></span><span class="envelope"></span><span class="tile-title">Reporter - Finanace Conslidated</span></div><span class="tech portal"></span><div class="actions"><span><svg width="12" height="12"><use href="#i-wrench"/></svg></span><span><svg width="12" height="12"><use href="#i-doc"/></svg></span><span><svg width="12" height="12"><use href="#i-chart"/></svg></span></div></article>

  <article class="tile is-draft"><div class="tile-head"><span class="marker"></span><span class="envelope"></span><span class="tile-title">Sort</span></div><div class="tile-band"></div><span class="tech portal"></span><div class="actions"><span><svg width="12" height="12"><use href="#i-wrench"/></svg></span><span><svg width="12" height="12"><use href="#i-doc"/></svg></span><span><svg width="12" height="12"><use href="#i-chart"/></svg></span></div></article>
  <article class="tile"><div class="tile-head"><span class="marker"></span><span class="envelope"></span><span class="tile-title">Sort Utilization</span></div><span class="tech viz"></span><div class="actions"><span><svg width="12" height="12"><use href="#i-wrench"/></svg></span><span><svg width="12" height="12"><use href="#i-doc"/></svg></span><span><svg width="12" height="12"><use href="#i-chart"/></svg></span></div></article>
</main>

<aside class="popover">
  <h3>Statement of Reccharge Online Tool</h3>
  <p>This tool is used for approval of intercomp any recharges. Scope: Globel.</p>
</aside>

<footer class="footer">
  <div class="help"><svg width="16" height="13" viewBox="0 0 16 13"><path d="M8 1C4.1 1 1 3.2 1 6c0 1.3.7 2.5 1.9 3.4L2.3 12l3-1.7c.8.2 1.7.3 2.7.3 3.9 0 7-2.2 7-4.6S11.9 1 8 1z" fill="none" stroke="#fff" stroke-width="1.3"/></svg>HELP &amp; FEEDBACK</div>
  <div class="copyright">COPYRIGHTS 2015. CSU M&amp;I. ALL RIGHTS RESERVED.</div>
  <div class="foot-brand"><i></i>CSUM&amp;I</div>
  <div class="version">C8</div>
</footer>
</body>
</html>
```